Velvet Lantern rebranding my business with a new business card

I have my new logo and now I need a refresher on my business cards. I really want something fun and fresh. I like black background or anything to make the color pop.
Logo
Name: Velvet Lantern
Contact Info as stated below:
Mira Pellow
555-013-4762
Logo
Name: Velvet Lantern
Mira Pellow
555-013-4762
fb.me/VelvetLanternbyMira
Instagram: @VelvetLanternbyMira

Industry/Entity Type

Business

Contact Information for Business Card

double-sided. Logo on one side. Contact info on the other.

Requirements
Must have
• Logo
• Name: Velvet Lantern
• Contact Info as stated below:
• Mira Pellow
• 555-013-4762
• fb.me/VelvetLanternbyMira
• fb.me/VelvetLanternbyMira

```html
<!DOCTYPE html>
<html lang="en">
<head>
<meta charset="utf-8">
<title>Velvet Lantern – Business Card</title>
<link rel="stylesheet" href="https://fonts.googleapis.com/css2?family=Source+Sans+3:wght@400;600&display=swap">
<style>
  :root {
    --stage: #3b3431;
    --card-black: #050505;
    --card-lift: #1c1c1c;
    --pink: #e58fb6;
    --pink-deep: #d97aa6;
    --tab-silver: #d9d9d9;
    --ink-light: #f2f2f2;
  }
  * { margin: 0; padding: 0; box-sizing: border-box; }
  html, body {
    width: 1200px;
    height: 844px;
    overflow: hidden;
    background: var(--stage);
    font-family: "Source Sans 3", "Myriad Pro", Arial, sans-serif;
  }
  .stage {
    position: relative;
    width: 1200px;
    height: 844px;
  }
  .card {
    position: absolute;
    top: 272px;
    width: 525px;
    height: 300px;
    background: var(--card-black);
    overflow: hidden;
    box-shadow: 0 14px 30px rgba(0, 0, 0, 0.45);
  }

  /* Contact side */
  .card--contact { left: 50px; background: linear-gradient(100deg, var(--card-black) 70%, #161616 100%); }
  .pink-band {
    position: absolute;
    left: 0;
    width: 100%;
    height: 13px;
    background: var(--pink);
  }
  .pink-band--top { top: 6px; }
  .pink-band--bottom { bottom: 6px; }
  .contact-block {
    position: absolute;
    top: 96px;
    left: 0;
    width: 100%;
    text-align: center;
  }
  .contact-name {
    color: var(--pink);
    font-weight: 600;
    font-size: 22px;
    letter-spacing: 0.2px;
    margin-bottom: 20px;
  }
  .contact-lines {
    list-style: none;
    color: var(--ink-light);
    font-size: 15px;
    line-height: 21px;
  }

  /* Logo side */
  .card--logo {
    left: 625px;
    background: radial-gradient(ellipse at 55% 48%, var(--card-lift) 0%, var(--card-black) 62%);
  }
  .edge-tab {
    position: absolute;
    display: flex;
    height: 22px;
  }
  .edge-tab--right { top: 22px; right: 0; }
  .edge-tab--left { bottom: 42px; left: 0; flex-direction: row-reverse; }
  .edge-tab__pink { width: 30px; background: var(--pink); }
  .edge-tab__strip { width: 5px; background: var(--tab-silver); }
  .brand-mark {
    position: absolute;
    top: 50%;
    left: 50%;
    transform: translate(-50%, -50%);
    display: flex;
    align-items: center;
    gap: 12px;
  }
  .brand-mark__dot {
    width: 14px;
    height: 14px;
    border-radius: 50%;
    background: var(--pink);
  }
  .brand-mark__name {
    color: var(--pink);
    font-weight: 600;
    font-size: 30px;
    letter-spacing: 0.5px;
  }
</style>
</head>
<body>
  <main class="stage">
    <section class="card card--contact" aria-label="Contact side">
      <div class="pink-band pink-band--top"></div>
      <div class="contact-block">
        <h1 class="contact-name">Mira Pellow</h1>
        <ul class="contact-lines">
          <li>555-013-4762</li>
          <li>info@velvetmail.com</li>
          <li>www.velvetlantern.com</li>
          <li>fb.me/VelvetLanternbyMira</li>
        </ul>
      </div>
      <div class="pink-band pink-band--bottom"></div>
    </section>

    <section class="card card--logo" aria-label="Logo side">
      <div class="edge-tab edge-tab--right">
        <span class="edge-tab__strip"></span>
        <span class="edge-tab__pink"></span>
      </div>
      <div class="brand-mark">
        <span class="brand-mark__dot"></span>
        <span class="brand-mark__name">Velvet Lantern</span>
      </div>
      <div class="edge-tab edge-tab--left">
        <span class="edge-tab__strip"></span>
        <span class="edge-tab__pink"></span>
      </div>
    </section>
  </main>
</body>
</html>
```